Alcohol brand needs design for gift tin packaging

We need a new design for the gift tins for our vodka brand. The bottles are in the shape of an oil barrel and the tins are also in the same shape. We would like to see the use of our logo. The gift tin needs to have a premium look.
Images of our bottles, logo and the gift tin are attached.

```html
<!DOCTYPE html>
<html lang="en">
<head>
<meta charset="utf-8">
<title>Tidewater Drum Vodka – Gift Tin Wrap</title>
<link rel="stylesheet" href="https://fonts.googleapis.com/css2?family=Rubik+Dirt&family=Oswald:wght@500&display=swap">
<style>
  :root {
    --backdrop: #d9d9d9;
    --drum-black: #1e1e1f;
    --drum-sheen: #3a3a3c;
    --rust: #f0553a;
    --rust-soft: #c9452f;
  }
  * { box-sizing: border-box; margin: 0; padding: 0; }
  html, body { width: 1200px; height: 780px; overflow: hidden; }
  body { background: var(--backdrop); position: relative; font-family: "Rubik Dirt", "Oswald", sans-serif; color: var(--rust); }

  .tin-wrap {
    position: absolute; left: 60px; top: 90px; width: 1080px; height: 600px;
    background: linear-gradient(90deg, var(--drum-black) 0%, var(--drum-sheen) 25%, var(--drum-black) 50%, var(--drum-sheen) 75%, var(--drum-black) 100%);
    overflow: hidden;
  }
  .sea-chart { position: absolute; inset: 0; }
  .hatch-band { position: absolute; left: 0; right: 0; height: 10px; border-top: 1px solid var(--rust); border-bottom: 1px solid var(--rust); opacity: .7; }
  .hatch-band--top { top: 12px; }
  .hatch-band--bottom { bottom: 12px; }
  .rib { position: absolute; left: 0; right: 0; height: 8px; background: #111; opacity: .75; }
  .rib--upper { top: 196px; }
  .rib--lower { top: 392px; }

  .art { position: absolute; }
  .label-text { position: absolute; line-height: .95; text-transform: uppercase; white-space: nowrap; }

  .since { left: 40px; top: 50px; font-size: 30px; transform: rotate(-14deg); text-align: center; }
  .vodka { left: 170px; top: 80px; font-size: 62px; transform: rotate(-6deg); }
  .caution { left: 110px; top: 150px; font-size: 36px; transform: rotate(-10deg); letter-spacing: 2px; }
  .brand-name { left: 330px; top: 400px; font-size: 72px; transform: rotate(-8deg); letter-spacing: 2px; }
  .strength { left: 60px; top: 470px; font-size: 34px; transform: rotate(-10deg); text-align: center; }
  .strength small { display: block; font-size: 22px; }
</style>
</head>
<body>
  <section class="tin-wrap">
    <svg class="sea-chart" width="1080" height="600" role="img" aria-label="Topographic sea chart with contour lines and grid">
      <rect width="1080" height="600" fill="var(--rust)" opacity="0.06"/>
      <g stroke="var(--rust)" stroke-width="0.8" opacity="0.45">
        <line x1="135" y1="0" x2="135" y2="600"/><line x1="270" y1="0" x2="270" y2="600"/>
        <line x1="405" y1="0" x2="405" y2="600"/><line x1="540" y1="0" x2="540" y2="600"/>
        <line x1="675" y1="0" x2="675" y2="600"/><line x1="810" y1="0" x2="810" y2="600"/>
        <line x1="945" y1="0" x2="945" y2="600"/>
        <line x1="0" y1="150" x2="1080" y2="150"/><line x1="0" y1="300" x2="1080" y2="300"/>
        <line x1="0" y1="450" x2="1080" y2="450"/>
      </g>
    </svg>
    <div class="hatch-band hatch-band--top"></div>
    <div class="hatch-band hatch-band--bottom"></div>
    <div class="rib rib--upper"></div>
    <div class="rib rib--lower"></div>

    <svg class="art" style="left:140px;top:-30px" width="240" height="60" role="img" aria-label="Skull illustration at top edge"><rect width="240" height="60" rx="30" fill="var(--rust)" opacity="0.75"/></svg>
    <svg class="art" style="left:180px;top:230px" width="150" height="150" role="img" aria-label="Compass rose illustration"><circle cx="75" cy="75" r="70" fill="var(--rust)" opacity="0.25"/></svg>
    <svg class="art" style="left:470px;top:220px" width="110" height="140" role="img" aria-label="Sailing ship illustration"><rect width="110" height="140" rx="8" fill="var(--rust)" opacity="0.22"/></svg>
    <svg class="art" style="left:640px;top:230px" width="180" height="130" role="img" aria-label="Sailing ships illustration"><rect width="180" height="130" rx="8" fill="var(--rust)" opacity="0.22"/></svg>
    <svg class="art" style="left:880px;top:250px" width="160" height="100" role="img" aria-label="Sea kraken tentacles illustration"><rect width="160" height="100" rx="8" fill="var(--rust)" opacity="0.22"/></svg>
    <svg class="art" style="left:420px;top:440px" width="260" height="160" role="img" aria-label="Large distressed skull illustration"><rect width="260" height="180" rx="90" fill="var(--rust)" opacity="0.8"/></svg>

    <p class="label-text since">Since<br>2017</p>
    <p class="label-text vodka">Vodka</p>
    <p class="label-text caution">Drink Cautiously</p>
    <p class="label-text brand-name">Tidewater Drum</p>
    <p class="label-text strength">40%<small>Alcohol</small></p>
  </section>
</body>
</html>
```